Business Card for a New Zealand IT Startup

I need a business card for VELTA Holdings. We are a young startup based in New Zealand working in internet marketing and web development. The design should have some element connected to New Zealand, such as wave, koru or silver fern, just don't use a kiwi bird.

```html
<!DOCTYPE html>
<html lang="en">
<head>
<meta charset="utf-8">
<title>VELTA Holdings – Business Card</title>
<link rel="stylesheet" href="https://fonts.googleapis.com/css2?family=Jost:wght@400;500;600&family=Roboto:wght@400&display=swap">
<style>
  :root {
    --brand-blue: #0070ba;
    --brand-orange: #f15a26;
    --card-white: #ffffff;
    --backdrop: #e9eaec;
  }
  * { margin: 0; padding: 0; box-sizing: border-box; }
  html, body {
    width: 1125px;
    height: 1200px;
    overflow: hidden;
    background: var(--backdrop);
    font-family: "Jost", sans-serif;
  }
  .card {
    position: absolute;
    left: 171px;
    width: 826px;
    height: 471px;
    border-radius: 25px;
    overflow: hidden;
  }
  .card--front { top: 106px; background: var(--card-white); }
  .card--back { top: 639px; background: var(--brand-orange); }

  .front-band { position: absolute; inset: 0; width: 100%; height: 100%; }

  .holder { position: absolute; left: 55px; top: 52px; }
  .holder__name {
    color: var(--brand-blue);
    font-size: 31px;
    font-weight: 500;
    line-height: 1;
    letter-spacing: 0.5px;
  }
  .holder__role {
    color: var(--brand-orange);
    font-size: 21px;
    font-weight: 400;
    line-height: 1;
    margin-top: 4px;
  }

  .wordmark {
    position: absolute;
    right: 58px;
    top: 52px;
    color: var(--brand-blue);
    font-weight: 600;
    text-align: center;
    line-height: 1;
  }
  .wordmark__main { font-size: 92px; letter-spacing: 2px; }
  .wordmark__sub { font-size: 26px; letter-spacing: 13px; margin-top: 8px; margin-right: -13px; }

  .contact {
    position: absolute;
    left: 55px;
    top: 254px;
    color: var(--card-white);
    font-size: 20px;
    line-height: 25px;
  }
  .contact__address { margin-bottom: 12px; }
  .contact__list { list-style: none; }
  .contact__item { display: flex; align-items: center; gap: 12px; height: 26.5px; }
  .contact__icon { width: 18px; height: 18px; fill: var(--card-white); flex: none; }

  .back-mark {
    position: absolute;
    left: 0;
    right: 0;
    top: 150px;
    text-align: center;
    color: var(--card-white);
    font-weight: 600;
    font-size: 100px;
    line-height: 1;
    letter-spacing: 4px;
  }
  .back-site {
    position: absolute;
    left: 0;
    right: 0;
    top: 393px;
    text-align: center;
    color: var(--card-white);
    font-family: "Roboto", sans-serif;
    font-size: 19px;
    letter-spacing: 8px;
  }
</style>
</head>
<body>

<section class="card card--front">
  <svg class="front-band" viewBox="0 0 826 471" preserveAspectRatio="none" role="img" aria-label="Blue wave decoration across the lower card">
    <path fill="var(--brand-blue)" d="M0,220 C140,160 280,190 400,270 C520,350 640,430 826,330 L826,471 L0,471 Z"/>
  </svg>

  <div class="holder">
    <p class="holder__name">MARA DOYLE</p>
    <p class="holder__role">CEO/FOUNDER</p>
  </div>

  <div class="wordmark">
    <p class="wordmark__main">VELTA</p>
    <p class="wordmark__sub">HOLDINGS</p>
  </div>

  <div class="contact">
    <p class="contact__address">4120 Harbour Crescent<br>Tauranga, Bay of Plenty 3110</p>
    <ul class="contact__list">
      <li class="contact__item">
        <svg class="contact__icon" viewBox="0 0 24 24" aria-hidden="true"><path d="M6.6 10.8a15.1 15.1 0 0 0 6.6 6.6l2.2-2.2a1 1 0 0 1 1-.25 11.4 11.4 0 0 0 3.6.57 1 1 0 0 1 1 1V20a1 1 0 0 1-1 1A17 17 0 0 1 3 4a1 1 0 0 1 1-1h3.5a1 1 0 0 1 1 1c0 1.25.2 2.45.57 3.57a1 1 0 0 1-.25 1z"/></svg>
        <span>021 584 3927</span>
      </li>
      <li class="contact__item">
        <svg class="contact__icon" viewBox="0 0 24 24" aria-hidden="true"><path d="M7 1h10a2 2 0 0 1 2 2v18a2 2 0 0 1-2 2H7a2 2 0 0 1-2-2V3a2 2 0 0 1 2-2zm0 3v14h10V4zm5 15.2a1.2 1.2 0 1 0 0 2.4 1.2 1.2 0 0 0 0-2.4z"/></svg>
        <span>027 316 8450</span>
      </li>
      <li class="contact__item">
        <svg class="contact__icon" viewBox="0 0 24 24" aria-hidden="true"><path d="M2 6h20v12H2zm2 1.5 8 5.5 8-5.5V7H4z"/></svg>
        <span>mara@veltaholdings.com</span>
      </li>
      <li class="contact__item">
        <svg class="contact__icon" viewBox="0 0 24 24" aria-hidden="true"><path d="M12 2a10 10 0 1 0 0 20 10 10 0 0 0 0-20zm-1 17.9A8 8 0 0 1 4.2 10.8L9 15.5v1a2 2 0 0 0 2 2zm6.9-2.5A2 2 0 0 0 16 16h-1v-3a1 1 0 0 0-1-1H8v-2h2a1 1 0 0 0 1-1V7h2a2 2 0 0 0 2-2v-.4a8 8 0 0 1 2.9 12.8z"/></svg>
        <span>www.veltaholdings.com</span>
      </li>
    </ul>
  </div>
</section>

<section class="card card--back">
  <p class="back-mark">VELTA</p>
  <p class="back-site">www.veltaholdings.com</p>
</section>

</body>
</html>
```